Velmorique Shampoo

Velmorique shampoo is aimed to be a "novelty" item, with an intriguing mix of ingredients including but not limited to CBD & caffeine. We want a design that has a unique way of portraying "velmorique". Get creative with this one. We want the designers to get creative and think outside of the box, and maybe even get a little crazy (but not too crazy), because that's what the premise of the shampoo is; out of the box thinking -- "velmorique". Try to incorporate what you think of when you hear the word velmorique.

On the front of the bottle is where the main design will be shown. On the back will be the ingredients list, and will have a bit more information. The design should flow well with a darkish-brown bottle, pictured in the attachments called "bottle-size-template".

Avoid simple designs. We want our shampoo to stand out, not stand on the shelves. Get creative. IMPORTANT NOTE: Please do not use / inspire from the attachments called "bottle-size-template", as these are to show you what the bottle looks like, and what the label will look like on the bottle. DO NOT MAKE YOUR DESIGN BASED FROM THOSE ATTACHMENTS!

If you are feeling like a winner, you can even insert the correct ingredients list: Purified water (aqua), pure virgin hemp seed oil, green tea essential oil, green tea extract, aloe vera, ginseng extract, cam-phor essential oil, glycerin(vegetable), borage seed oil, lauryl glucoside, coconut oil, yucca extract, dermochlorella extract(seaweed based), nettle extract, coco glucoside, jojoba oil, awapuhi, soluble natural plant collagen, wheat germ glycerides (gluten free), echinacea extract, licorice root extract, cocoa butter, ivy extract, soy protein non-GMO), ascorbyl tetraisopalmitate (palm based), golden seal extract, behenic acid (natural based) guar gum, ylang ylang extract, sea salt.

```html
<!DOCTYPE html>
<html lang="en">
<head>
<meta charset="utf-8">
<title>Velmorique Hair Shampoo – Label</title>
<link href="https://fonts.googleapis.com/css2?family=Open+Sans:wght@400;600;700&family=Varela+Round&display=swap" rel="stylesheet">
<style>
  :root {
    --stage: #d6d7d8;
    --magenta: #a3205d;
    --navy: #1b1944;
    --deep: #140f34;
    --glow: #c2347a;
    --violet: #4a2a7a;
    --white: #ffffff;
  }
  * { box-sizing: border-box; margin: 0; padding: 0; }
  html, body {
    width: 1200px; height: 568px; overflow: hidden;
    background: var(--stage);
  }
  .label {
    position: absolute; left: 109px; top: 109px;
    width: 982px; height: 350px;
    background: var(--white);
    box-shadow: 6px 8px 14px rgba(0,0,0,0.35);
    font-family: "Open Sans", sans-serif;
    color: var(--white);
  }
  .side-panel {
    position: absolute; top: 0; width: 107px; height: 350px;
    background: var(--magenta);
  }
  .side-panel--left { left: 0; }
  .side-panel--right { left: 876px; width: 106px; }
  .side-art {
    position: absolute; left: 11px; top: 15px; width: 88px; height: 320px;
    border-radius: 46% 42% 40% 48% / 30% 28% 34% 32%;
    border: 3px solid var(--white);
    background: radial-gradient(ellipse at 50% 50%, rgba(255,255,255,0.28), rgba(255,255,255,0.12) 70%);
  }
  .divider {
    position: absolute; top: 0; width: 3px; height: 350px; background: var(--white);
  }
  .divider--left { left: 107px; }
  .divider--right { left: 873px; }

  .wrap-area {
    position: absolute; left: 110px; top: 0; width: 763px; height: 350px;
    background:
      radial-gradient(ellipse 230px 200px at 570px 185px, rgba(200,50,120,0.85), rgba(150,40,120,0.45) 50%, transparent 85%),
      radial-gradient(ellipse 180px 160px at 200px 250px, rgba(170,40,110,0.5), transparent 75%),
      radial-gradient(ellipse 420px 260px at 380px 175px, var(--violet), transparent 85%),
      var(--navy);
    overflow: hidden;
  }
  .front-art {
    position: absolute; left: 469px; top: 108px; width: 216px; height: 240px;
    border-radius: 48% 48% 42% 42%;
    background: radial-gradient(ellipse at 50% 45%, rgba(214,60,140,0.75), rgba(160,40,120,0.45) 55%, transparent 78%);
  }

  .intro {
    position: absolute; left: 11px; top: 41px; width: 344px;
    font-size: 9.5px; line-height: 12.2px; text-align: justify;
  }
  .panel { position: absolute; left: 11px; }
  .ingredients { top: 104px; width: 344px; }
  .direction { top: 225px; width: 263px; }
  .section-title {
    background: var(--white); color: var(--magenta);
    font-size: 8.5px; font-weight: 700; letter-spacing: 1.6px;
    text-align: center; height: 11px; line-height: 11px;
  }
  .section-box {
    border: 2px solid var(--white); border-top: 0;
    padding: 3px 5px;
    font-size: 8.6px; line-height: 11.7px; text-align: justify;
  }
  .direction .section-box { text-align: left; font-size: 9px; line-height: 12px; height: 47px; }

  .code-box {
    position: absolute; background: var(--white); color: var(--magenta);
    font-size: 9px; display: flex; align-items: center; justify-content: center;
  }
  .code-box--qr { left: 226px; top: 294px; width: 48px; height: 48px; }
  .code-box--bar { left: 286px; top: 228px; width: 69px; height: 114px; }
  .code-box--bar span { transform: rotate(-90deg); white-space: nowrap; }

  .brand-box {
    position: absolute; left: 477px; top: 41px; width: 190px; height: 59px;
    border: 1.5px solid var(--white);
    text-align: center;
  }
  .brand-name {
    font-family: "Varela Round", sans-serif; font-weight: 400;
    font-size: 27px; line-height: 30px; margin-top: 5px;
  }
  .brand-sub { font-size: 14px; line-height: 16px; }
  .front-info {
    position: absolute; left: 501px; top: 279px; width: 132px;
    text-align: center;
  }
  .claim { font-size: 11.5px; line-height: 15px; padding-bottom: 3px; border-bottom: 1px solid var(--white); }
  .spec { font-size: 10.5px; line-height: 13px; margin-top: 7px; }
</style>
</head>
<body>
  <div class="label">
    <div class="side-panel side-panel--left">
      <div class="side-art" role="img" aria-label="White line drawing of a brain seen from above"></div>
    </div>
    <div class="divider divider--left"></div>

    <div class="wrap-area">
      <div class="front-art" role="img" aria-label="Glowing pink brain image bursting with light"></div>

      <p class="intro">This product is specially made with hemp seed oil, which is know for its nutritional and medicinal properties. This ingredient has been rediscovered as a beauty aid due to its moisturizing and anti-again effects. it is a rich source of essential fatty acids, including omega-3, which helps replenish and lubricates the hair the natural way.</p>

      <div class="panel ingredients">
        <h2 class="section-title">INGREDIENTS LIST:</h2>
        <p class="section-box">Purified water (aqua), pure virgin hemp seed oil, green tea essential oil, green tea extract, aloe vera, ginseng extract, cam-phor essential oil, glycerin (vegetable), borage seed oil, lauryl glucoside, coconut oil, yucca extract, dermochlorella extract (seaweed based), nettle extract, coco glucoside, jojoba oil, awapuhi, soluble natural plant collagen, wheat germ glycerides (gluten free), echinacea extract, licorice root extract, cocoa butter, ivy extract, soy protein non-GMO), ascorbyl tetraisopalmitate (palm based), golden seal extract, behenic acid (natural based) guar gum, ylang ylang extract, sea salt.</p>
      </div>

      <div class="panel direction">
        <h2 class="section-title">DIRECTION</h2>
        <p class="section-box">Apply hemp Shampoo to wet hair. Massage into scalp and hair, leaves for 23 minutes. Rinse and repeat if necessary. Recommended for daily use with Hemp Conditioner.</p>
      </div>

      <div class="code-box code-box--qr">QR</div>
      <div class="code-box code-box--bar"><span>Bar code</span></div>

      <div class="brand-box">
        <h1 class="brand-name">velmorique</h1>
        <p class="brand-sub">Hair Shampoo</p>
      </div>

      <div class="front-info">
        <p class="claim">Strengthnes Weak Hair</p>
        <p class="spec">For All Hair Types<br>500ml/17.7 fl.oz</p>
      </div>
    </div>

    <div class="divider divider--right"></div>
    <div class="side-panel side-panel--right">
      <div class="side-art" role="img" aria-label="White line drawing of a brain seen from above"></div>
    </div>
  </div>
</body>
</html>
```